Classy, Elegant, Simple Business Card Design

Looking to have a classy, simple, and elegant design. Want a top notch designed business card. I really like the look of the new torvane credit card. I also like the design I attached. I am trying to reach 21-29 year old females for booking us for there wedding or event. We offer Disc Jockey Service, Photo Booth Rentals, and Uplighting .

Target Market(s)

21-28 year old females

Contact Information for Business Card

Has to have logo, website, email, and phone number

Font styles to use
Other font styles liked:
• open to font choice, modern, clean
Designer to choose
33a6d7
0791cd
0555a3
ffffff

Requirements
Must have
• Has to have logo, website, email, and phone number
Nice to have
• I really like the design of the new torvane credit card. I also included my logo and some designs I like
Should not have
• clutter or too much info

```html
<!DOCTYPE html>
<html lang="en">
<head>
<meta charset="utf-8">
<title>Tidecrest Event Group – Business Card</title>
<link rel="stylesheet" href="https://fonts.googleapis.com/css2?family=Montserrat:wght@500;600;700&family=Poppins:wght@400;500&display=swap">
<style>
  :root {
    --navy: #0f2a57;
    --blue: #0791cd;
    --sky: #33a6d7;
    --royal: #0555a3;
    --white: #ffffff;
    --ink: #1c2c4a;
    --backdrop: #e9ecf1;
  }
  * { margin: 0; padding: 0; box-sizing: border-box; }
  html, body { width: 1200px; height: 912px; overflow: hidden; }
  body {
    background: var(--backdrop);
    position: relative;
    font-family: "Poppins", sans-serif;
  }
  .card {
    position: absolute;
    width: 620px;
    height: 354px;
    border-radius: 18px;
    overflow: hidden;
    box-shadow: 0 10px 30px rgba(15, 42, 87, 0.18);
  }
  /* Front card */
  .card--front {
    left: 70px;
    top: 70px;
    background: var(--navy);
  }
  .brand {
    display: flex;
    align-items: center;
    gap: 14px;
    font-family: "Montserrat", sans-serif;
    font-weight: 600;
    letter-spacing: 0.04em;
  }
  .brand__dot {
    width: 22px;
    height: 22px;
    border-radius: 50%;
    background: var(--sky);
    flex: none;
  }
  .brand__name {
    font-size: 30px;
    line-height: 1.15;
    text-transform: uppercase;
  }
  .card--front .brand {
    position: absolute;
    left: 0; right: 0;
    top: 120px;
    justify-content: center;
  }
  .card--front .brand__name { color: var(--sky); text-align: left; }
  .card--front .website {
    position: absolute;
    right: 70px;
    bottom: 58px;
    color: var(--white);
    font-size: 17px;
    letter-spacing: 0.12em;
  }
  /* Back card */
  .card--back {
    left: 510px;
    top: 488px;
    background: var(--white);
  }
  .card--back .wave {
    position: absolute;
    inset: 0;
  }
  .card--back .brand {
    position: absolute;
    left: 46px;
    top: 126px;
  }
  .card--back .brand__name { color: var(--blue); font-size: 28px; }
  .person {
    position: absolute;
    right: 34px;
    top: 26px;
    text-align: right;
  }
  .person__name {
    font-family: "Montserrat", sans-serif;
    font-weight: 700;
    font-size: 22px;
    color: var(--blue);
    letter-spacing: 0.02em;
  }
  .person__role {
    font-size: 13px;
    color: var(--ink);
  }
  .contact {
    position: absolute;
    right: 30px;
    top: 128px;
    list-style: none;
    text-align: right;
    color: var(--white);
    font-size: 14px;
    line-height: 1.55;
  }
  .contact li { display: flex; justify-content: flex-end; align-items: center; gap: 8px; }
  .contact svg { width: 12px; height: 12px; flex: none; }
  .contact .address { margin-top: 10px; display: block; padding-right: 20px; }
</style>
</head>
<body>

<section class="card card--front">
  <div class="brand">
    <span class="brand__dot"></span>
    <span class="brand__name">Tidecrest<br>Event Group</span>
  </div>
  <p class="website">www.tidecrest.com</p>
</section>

<section class="card card--back">
  <svg class="wave" viewBox="0 0 620 354" preserveAspectRatio="none" aria-hidden="true">
    <path d="M0,300 C180,292 300,290 352,232 C412,166 420,98 540,90 C580,88 610,90 620,92 L620,354 L0,354 Z" fill="var(--navy)"/>
    <path d="M0,288 C170,282 286,278 338,224 C396,162 404,88 532,78 C580,74 610,76 620,78" fill="none" stroke="var(--navy)" stroke-width="4"/>
    <path d="M0,312 C190,306 310,302 370,244 C410,205 420,168 430,150" fill="none" stroke="var(--sky)" stroke-width="12"/>
  </svg>

  <div class="brand">
    <span class="brand__dot"></span>
    <span class="brand__name">Tidecrest<br>Event Group</span>
  </div>

  <div class="person">
    <p class="person__name">DARREN HOLT</p>
    <p class="person__role">Managing Partner</p>
  </div>

  <ul class="contact">
    <li>615-555-0172
      <svg viewBox="0 0 24 24"><path d="M6.6 10.8a15 15 0 0 0 6.6 6.6l2.2-2.2a1 1 0 0 1 1-.25 11.4 11.4 0 0 0 3.6.57 1 1 0 0 1 1 1V20a1 1 0 0 1-1 1A17 17 0 0 1 3 4a1 1 0 0 1 1-1h3.5a1 1 0 0 1 1 1c0 1.25.2 2.45.57 3.57a1 1 0 0 1-.25 1z" fill="var(--white)"/></svg>
    </li>
    <li>info@tidecrest.com
      <svg viewBox="0 0 24 24"><rect x="3" y="5" width="18" height="14" rx="2" fill="none" stroke="var(--white)" stroke-width="2"/><path d="M3 7l9 6 9-6" fill="none" stroke="var(--white)" stroke-width="2"/></svg>
    </li>
    <li>www.tidecrest.com
      <svg viewBox="0 0 24 24"><circle cx="12" cy="12" r="9" fill="none" stroke="var(--white)" stroke-width="2"/><path d="M3 12h18M12 3c3 3 3 15 0 18M12 3c-3 3-3 15 0 18" fill="none" stroke="var(--white)" stroke-width="1.5"/></svg>
    </li>
    <li class="address">418 W Harbor Ave.,<br>Los Angeles, CA 90012</li>
  </ul>
</section>

</body>
</html>
```